Website for BrightlineLabs presentation

We need a new website, ideally as a wordpress there, for BrightlineLabs - we focus on machine learning, big data, data science and data analytics. This website should have two main sections - team presentation, introduction and offered services as static pages, and a blog section.

Target Market(s)

Companies which would like to hire the consultants for data science

Industry/Entity Type

Data Service

Font styles to use
Sans Serif

Colors

Designer to choose colors to be used in the design.

Requirements
Must have
• Wordpress template, blog and presentation pages, nice background images, incorporate the existing logo from brief
Nice to have
• match the word and ppt existing templates for brightline labs

```html
<!DOCTYPE html>
<html lang="en">
<head>
<meta charset="utf-8">
<title>BrightlineLabs</title>
<link href="https://fonts.googleapis.com/css2?family=Lato:ital,wght@0,400;0,700;0,900;1,400&display=swap" rel="stylesheet">
<style>
:root{
  --blue-900:#0d4fa6;
  --blue-700:#1565c0;
  --blue-600:#1976d2;
  --blue-500:#1e88e5;
  --blue-300:#64b5f6;
  --accent:#1a73c9;
  --ink:#3c3c3c;
  --muted:#6b6b6b;
  --light:#ececec;
  --footer:#e4e4e4;
  --white:#ffffff;
}
*{margin:0;padding:0;box-sizing:border-box}
html,body{width:1200px;height:3333px;overflow:hidden;background:var(--white)}
body{font-family:'Lato',sans-serif;color:var(--ink)}
.page{position:relative;width:1200px;height:3333px;overflow:hidden}
.abs{position:absolute}

/* header */
.site-header{position:absolute;left:0;top:0;width:1200px;height:94px;background:var(--white);z-index:2;box-shadow:0 1px 4px rgba(0,0,0,.08)}
.brand{position:absolute;left:185px;top:28px;display:flex;align-items:center;gap:12px;font-weight:900;font-size:26px;color:var(--blue-700)}
.brand-mark{width:30px;height:30px;border-radius:50%;background:var(--blue-700)}
.main-nav{position:absolute;left:473px;top:38px;display:flex;gap:0;font-size:15px;font-weight:700;color:#444}
.main-nav span{margin-right:30px}
.main-nav .active{color:var(--accent);position:relative}
.main-nav .active::after{content:"";position:absolute;left:0;right:0;top:-38px;height:4px;background:var(--accent)}

/* hero */
.hero{position:absolute;left:0;top:94px;width:1200px;height:573px;background:radial-gradient(ellipse at 50% 40%,#2f8be6 0%,#1565c0 55%,#0b4a9c 100%)}
.hero-title{position:absolute;left:0;top:172px;width:1200px;text-align:center;color:var(--white);font-weight:900;font-size:42px;line-height:48px;text-transform:uppercase}
.hero-scroll{position:absolute;left:578px;top:408px;width:44px;height:44px;border:2px solid var(--white);border-radius:50%}
.hero-wave{position:absolute;left:0;bottom:0;width:1200px;height:50px}

/* welcome */
.welcome-photo{position:absolute;left:520px;top:742px;width:502px;height:376px;background:linear-gradient(135deg,#3d4d66 0%,#1f2c44 55%,#4a6fa8 100%)}
.welcome-card{position:absolute;left:184px;top:800px;width:429px;height:273px;background:var(--white);box-shadow:0 2px 12px rgba(0,0,0,.18);padding:38px 50px}
.welcome-card h2{font-size:24px;font-weight:700;color:#333;margin-bottom:14px}
.welcome-card p{font-size:12.5px;line-height:19px;color:var(--muted);margin-bottom:12px}
.btn-outline{display:inline-block;border:1.5px solid var(--accent);color:var(--accent);font-size:11px;font-weight:700;padding:8px 20px}

/* services */
.services{position:absolute;left:0;top:1182px;width:1200px;height:474px;background:linear-gradient(100deg,#ececec 0%,#f3f3f3 50%,#e8eef0 100%)}
.section-title{position:absolute;left:0;width:1200px;text-align:center;font-size:28px;font-weight:700;color:#444;text-transform:uppercase}
.service-row{position:absolute;left:182px;top:100px;width:840px;height:298px;display:flex}
.service{flex:1;color:var(--white);text-align:center;position:relative}
.service:nth-child(1){background:var(--blue-700)}
.service:nth-child(2){background:var(--blue-600)}
.service:nth-child(3){background:var(--blue-500)}
.service:nth-child(4){background:var(--blue-300)}
.service svg{position:absolute;left:50%;top:26px;margin-left:-46px}
.service h3{position:absolute;left:0;width:100%;top:140px;font-size:15px;font-weight:700}
.service p{position:absolute;left:20px;width:170px;top:172px;font-size:11px;line-height:14px;opacity:.9}
.service .btn-light{position:absolute;left:50%;top:232px;transform:translateX(-50%);border:1.5px solid var(--white);font-size:11px;font-weight:700;padding:7px 22px;white-space:nowrap}

/* team */
.member{position:absolute;top:1780px;width:260px;text-align:center}
.member .avatar{width:166px;height:166px;margin:0 auto;border:4px solid var(--accent);border-radius:50%;padding:6px}
.member .avatar div{width:100%;height:100%;border-radius:50%;background:radial-gradient(circle at 50% 40%,#b9a595 0%,#6f6a66 55%,#3d4550 100%)}
.member h4{margin-top:22px;font-size:19px;font-weight:400;color:var(--accent);text-transform:uppercase}
.member p{margin-top:6px;font-size:13px;line-height:19px;color:var(--muted);padding:0 20px}
.member .more{margin-top:10px;font-size:12px;font-weight:700;color:#333}

/* blogs */
.blogs{position:absolute;left:0;top:2142px;width:1200px;height:525px;background:linear-gradient(180deg,#1763bd 0%,#1e7fe0 100%)}
.blogs .section-title{color:var(--white)}
.blog-card{position:absolute;top:114px;width:394px;height:331px;background:var(--white)}
.blog-card .thumb{height:197px}
.blog-card h5{margin-top:18px;text-align:center;font-size:19px;font-weight:400;color:var(--accent)}
.blog-card p{margin:10px 30px 0;text-align:center;font-size:12px;line-height:17px;color:var(--muted)}
.blog-card .more{margin-top:10px;text-align:center;font-size:11px;font-weight:700;color:#333}
.blog-card .more b{color:var(--accent)}
.blog-side{position:absolute;top:114px;width:53px;height:331px;background:linear-gradient(180deg,#2a5f9b 0%,#2a5f9b 60%,#5aa6ef 60%,#5aa6ef 100%);opacity:.85}
.blog-arrow{position:absolute;top:262px}

/* testimonials */
.testi-title{color:var(--accent)}
.video{position:absolute;left:198px;top:2807px;width:398px;height:253px;background:linear-gradient(135deg,#5a4030 0%,#2c2a2c 50%,#1e2a3a 100%)}
.play{position:absolute;left:175px;top:102px;width:48px;height:48px;border-radius:50%;background:rgba(255,255,255,.9)}
.play::after{content:"";position:absolute;left:19px;top:14px;border-left:14px solid #333;border-top:10px solid transparent;border-bottom:10px solid transparent}
.frame-tl{position:absolute;left:187px;top:2795px;width:52px;height:40px;border-left:3px solid var(--accent);border-top:3px solid var(--accent)}
.frame-br{position:absolute;left:556px;top:3033px;width:52px;height:40px;border-right:3px solid var(--accent);border-bottom:3px solid var(--accent)}
.quote-mark{position:absolute;left:646px;top:2806px;font-size:64px;font-weight:900;color:var(--accent);line-height:64px}
.quote-text{position:absolute;left:649px;top:2862px;width:390px;font-style:italic;font-size:15px;line-height:25px;color:#555}
.quote-author{position:absolute;left:649px;top:2990px;font-size:14px;color:#333}
.dots{position:absolute;left:649px;top:3040px;display:flex;gap:6px;align-items:center}
.dots i{display:block;width:8px;height:8px;border-radius:50%;background:#cfcfcf}
.dots i.big{width:16px;height:16px;background:#9e9e9e}

/* footer */
.site-footer{position:absolute;left:0;top:3156px;width:1200px;height:177px;background:var(--footer)}
.footer-nav{position:absolute;left:188px;top:80px;display:flex;font-size:14px;font-weight:700;color:#444}
.footer-nav span{margin-right:30px}
.copyright{position:absolute;left:188px;top:110px;font-size:13px;color:#888}
.social{position:absolute;left:866px;top:72px;display:flex;gap:6px}
.social i{display:block;width:32px;height:32px;border:2px solid #333;border-radius:50%}
</style>
</head>
<body>
<div class="page">

  <header class="site-header">
    <div class="brand"><span class="brand-mark"></span>BrightlineLabs</div>
    <nav class="main-nav">
      <span class="active">HOME</span><span>ABOUT US</span><span>TEAM</span><span>SERVICES</span><span>BLOGS</span><span>CONTACT US</span>
    </nav>
  </header>

  <section class="hero" role="img" aria-label="Blue circuit-board brain background with network lines">
    <h1 class="hero-title">We provide machine learning,<br>big data, data science and<br>data analytics.</h1>
    <div class="hero-scroll">
      <svg width="40" height="40" viewBox="0 0 40 40"><path d="M13 17l7 7 7-7" fill="none" stroke="#fff" stroke-width="2.5"/></svg>
    </div>
    <svg class="hero-wave" viewBox="0 0 1200 50" preserveAspectRatio="none"><path d="M0 40 C40 20 70 38 110 26 C150 14 180 34 230 24 C280 14 310 30 360 22 C410 12 450 32 500 24 C550 16 590 30 640 20 C690 12 730 30 780 22 C830 14 870 32 920 24 C970 16 1010 30 1060 22 C1110 14 1150 30 1200 24 L1200 50 L0 50Z" fill="#fff"/></svg>
  </section>

  <section class="welcome">
    <div class="welcome-photo" role="img" aria-label="Hand touching a hexagon interface labelled machine learning"></div>
    <div class="welcome-card">
      <h2>WELCOME</h2>
      <p>Aemper mauris ipsum iaculis elit congue gravida elit mi egestas orci Curabitur pede Maecenas aliquet velit</p>
      <p>vel turpis Mauris neque metus malesuada nec ultricies sit amet porttitor mattis enim In massa libero interdum nec interdum vel blandit sed nulla In</p>
      <span class="btn-outline">READ MORE</span>
    </div>
  </section>

  <section class="services">
    <h2 class="section-title" style="top:42px">Our Services</h2>
    <div class="service-row">
      <div class="service">
        <svg width="92" height="100" viewBox="0 0 92 100"><circle cx="8" cy="12" r="6" fill="#fff"/><circle cx="20" cy="22" r="4" fill="#fff"/><circle cx="50" cy="58" r="38" fill="none" stroke="#fff" stroke-width="2.5"/><ellipse cx="50" cy="58" rx="20" ry="8" fill="none" stroke="#fff" stroke-width="2"/><ellipse cx="50" cy="58" rx="20" ry="8" transform="rotate(60 50 58)" fill="none" stroke="#fff" stroke-width="2"/><ellipse cx="50" cy="58" rx="20" ry="8" transform="rotate(-60 50 58)" fill="none" stroke="#fff" stroke-width="2"/></svg>
        <h3>DATA SCIENCE</h3>
        <p>Sed turpis mauris neque metus malesuada nec ultricies sit amet porttitor mattis</p>
        <span class="btn-light">READ MORE</span>
      </div>
      <div class="service">
        <svg width="92" height="100" viewBox="0 0 92 100"><circle cx="8" cy="12" r="6" fill="#fff"/><circle cx="20" cy="22" r="4" fill="#fff"/><circle cx="50" cy="58" r="38" fill="none" stroke="#fff" stroke-width="2.5"/><circle cx="50" cy="58" r="20" fill="none" stroke="#fff" stroke-width="2"/><ellipse cx="50" cy="58" rx="9" ry="20" fill="none" stroke="#fff" stroke-width="2"/><path d="M30 58h40" stroke="#fff" stroke-width="2"/></svg>
        <h3>BIG DATA</h3>
        <p>Sed turpis mauris neque metus malesuada nec ultricies sit amet porttitor mattis</p>
        <span class="btn-light">READ MORE</span>
      </div>
      <div class="service">
        <svg width="92" height="100" viewBox="0 0 92 100"><circle cx="8" cy="12" r="6" fill="#fff"/><circle cx="20" cy="22" r="4" fill="#fff"/><circle cx="50" cy="58" r="38" fill="none" stroke="#fff" stroke-width="2.5"/><circle cx="44" cy="62" r="11" fill="none" stroke="#fff" stroke-width="3" stroke-dasharray="4 3"/><circle cx="44" cy="62" r="4" fill="#fff"/><circle cx="60" cy="48" r="7" fill="none" stroke="#fff" stroke-width="2.5" stroke-dasharray="3 2"/></svg>
        <h3>MACHINE LEARNING</h3>
        <p>Sed turpis mauris neque metus malesuada nec ultricies sit amet porttitor mattis</p>
        <span class="btn-light">READ MORE</span>
      </div>
      <div class="service">
        <svg width="92" height="100" viewBox="0 0 92 100"><circle cx="8" cy="12" r="6" fill="#fff"/><circle cx="20" cy="22" r="4" fill="#fff"/><circle cx="50" cy="58" r="38" fill="none" stroke="#fff" stroke-width="2.5"/><circle cx="46" cy="54" r="13" fill="none" stroke="#fff" stroke-width="2.5"/><path d="M56 64l10 10" stroke="#fff" stroke-width="4" stroke-linecap="round"/><path d="M40 58v-4M45 58v-8M50 58v-6" stroke="#fff" stroke-width="2"/></svg>
        <h3>DATA ANALYTICS</h3>
        <p>Sed turpis mauris neque metus malesuada nec ultricies sit amet porttitor mattis</p>
        <span class="btn-light">READ MORE</span>
      </div>
    </div>
  </section>

  <section class="team">
    <h2 class="section-title" style="top:1704px">Our Team</h2>
    <div class="member" style="left:208px">
      <div class="avatar"><div role="img" aria-label="Portrait of team member"></div></div>
      <h4>Member Name</h4>
      <p>semper mauris ipsum iaculis elit congue gravida elit mi egestas orci Curabitur pede Maecenas aliquet</p>
      <div class="more">READ MORE</div>
    </div>
    <div class="member" style="left:472px;top:1776px">
      <div class="avatar"><div role="img" aria-label="Portrait of team member"></div></div>
      <h4>Member Name</h4>
      <p>semper mauris ipsum iaculis elit congue gravida elit mi egestas orci Curabitur pede Maecenas aliquet</p>
      <div class="more">READ MORE</div>
    </div>
    <div class="member" style="left:737px;top:1776px">
      <div class="avatar"><div role="img" aria-label="Portrait of team member"></div></div>
      <h4>Member Name</h4>
      <p>semper mauris ipsum iaculis elit congue gravida elit mi egestas orci Curabitur pede Maecenas aliquet</p>
      <div class="more">READ MORE</div>
    </div>
  </section>

  <section class="blogs">
    <h2 class="section-title" style="top:40px">Recent Blogs</h2>
    <div class="blog-side" style="left:0" role="img" aria-label="Partial previous blog card"></div>
    <div class="blog-side" style="left:1151px" role="img" aria-label="Partial next blog card"></div>
    <svg class="blog-arrow" style="left:136px" width="26" height="56" viewBox="0 0 26 56"><path d="M22 3L4 28l18 25" fill="none" stroke="#fff" stroke-width="2.5"/></svg>
    <svg class="blog-arrow" style="left:1070px" width="26" height="56" viewBox="0 0 26 56"><path d="M4 3l18 25L4 53" fill="none" stroke="#fff" stroke-width="2.5"/></svg>
    <article class="blog-card" style="left:204px">
      <div class="thumb" role="img" aria-label="Glowing digital head on dark blue background" style="background:radial-gradient(circle at 25% 45%,#3fa0ff 0%,#123a78 40%,#0a1a33 100%)"></div>
      <h5>Curabitur vel mi sit amet magna</h5>
      <p>Morbi diam mauris viverra in gravida eu mattis in ante Morbi eget arcu Morbi porta libero id ullamcorper nonummy</p>
      <div class="more">READ MORE <b>›</b></div>
    </article>
    <article class="blog-card" style="left:622px">
      <div class="thumb" role="img" aria-label="Hand holding glowing data icons on dark background" style="background:radial-gradient(circle at 50% 60%,#4e6a66 0%,#1d2a2c 55%,#0c1214 100%)"></div>
      <h5>Curabitur vel mi sit amet magna</h5>
      <p>Morbi diam mauris viverra in gravida eu mattis in ante Morbi eget arcu Morbi porta libero id ullamcorper nonummy</p>
      <div class="more">READ MORE <b>›</b></div>
    </article>
    <svg class="abs" style="left:0;bottom:0" width="1200" height="40" viewBox="0 0 1200 40" preserveAspectRatio="none"><path d="M0 30 C50 14 90 30 140 20 C190 10 230 28 280 18 C330 8 380 26 430 18 C480 10 520 26 570 18 C620 10 660 28 710 20 C760 12 800 26 850 18 C900 10 940 28 990 20 C1040 12 1090 28 1140 18 C1170 14 1190 20 1200 22 L1200 40 L0 40Z" fill="#fff"/></svg>
  </section>

  <section class="testimonials">
    <h2 class="section-title testi-title" style="top:2733px">Testimonials</h2>
    <div class="frame-tl"></div>
    <div class="video" role="img" aria-label="Team working together at laptops in a dim office"><div class="play"></div></div>
    <div class="frame-br"></div>
    <div class="quote-mark">“</div>
    <p class="quote-text">Aemper mauris ipsum iaculis elit congue gravida elit mi egestas orci Curabitur pedeMaecenas aliquet velit vel turpis Mauris neque metus malesuada nec ultricies sit amet porttitor mattis enim In massa libero</p>
    <div class="quote-author">BY AUTHOR NAME</div>
    <div class="dots"><i class="big"></i><i></i><i></i><i></i><i></i><i class="big"></i></div>
  </section>

  <footer class="site-footer">
    <svg class="abs" style="left:0;top:-20px" width="1200" height="40" viewBox="0 0 1200 40" preserveAspectRatio="none"><path d="M0 20 C40 8 80 24 130 14 C180 4 220 22 270 14 C320 6 360 22 410 14 C460 6 500 24 550 16 C600 8 640 22 690 14 C740 6 780 24 830 16 C880 8 920 22 970 14 C1020 6 1060 24 1110 16 C1150 10 1180 18 1200 16 L1200 40 L0 40Z" fill="#e4e4e4"/></svg>
    <nav class="footer-nav"><span>HOME</span><span>ABOUT US</span><span>TEAM</span><span>SERVICES</span><span>BLOGS</span><span>CONTACT US</span></nav>
    <div class="copyright">© 2018 Company Name  All right reserved</div>
    <div class="social" aria-label="Social links"><i></i><i></i><i></i><i></i></div>
  </footer>

</div>
</body>
</html>
```